Business Card Design for company

We want new business cards. We'd like something different-- yet still highly professional. Our tagline is Providing leadership, delivering success. Stock photos are ok, as long as they are relevant and look upscale.

Target Market(s)

Architecture/Business Management Consulting/Engineering Consulting

Contact Information for Business Card

dark gray background with pops of blue might be good, but you tell me. You're the designers. Rounded corners might be nice, but again, you tell me.

Font styles to use
Serif
Sans Serif

Colors
3276b5
5c5c5c
9d9d9d
fbfbfb

Requirements
Nice to have
• Something different, but still very professional.

```html
<!DOCTYPE html>
<html lang="en">
<head>
<meta charset="utf-8">
<title>Orven Partners – Business Card</title>
<link rel="stylesheet" href="https://fonts.googleapis.com/css2?family=Montserrat:wght@700&family=Work+Sans:wght@400;500&display=swap">
<style>
  :root {
    --backdrop: #262626;
    --card: #1c1c1d;
    --card-edge: #2e2e30;
    --blue: #3276b5;
    --ink: #fbfbfb;
    --muted: #9d9d9d;
    --logo-font: "Montserrat", sans-serif;
    --text-font: "Work Sans", sans-serif;
  }
  * { box-sizing: border-box; margin: 0; padding: 0; }
  html, body { width: 1200px; height: 900px; overflow: hidden; }
  body {
    background: var(--backdrop);
    position: relative;
    font-family: var(--text-font);
    color: var(--ink);
  }
  .card {
    position: absolute;
    left: 285px;
    width: 630px;
    height: 360px;
    border-radius: 22px;
    overflow: hidden;
    background: linear-gradient(160deg, #242426 0%, var(--card) 60%, #19191a 100%);
    box-shadow: 0 10px 28px rgba(0,0,0,.55), inset 0 0 0 1px var(--card-edge);
  }
  .card--front { top: 70px; }
  .card--back { top: 470px; }

  .wordmark {
    font-family: var(--logo-font);
    font-weight: 700;
    color: var(--ink);
    letter-spacing: .06em;
    line-height: 1.08;
    display: flex;
    align-items: center;
    gap: 14px;
  }
  .wordmark__dot {
    width: 22px; height: 22px;
    background: var(--blue);
    flex: none;
  }
  .wordmark__text { display: block; }

  .card--front .wordmark {
    position: absolute;
    top: 110px; left: 0; right: 0;
    justify-content: center;
    font-size: 44px;
  }
  .front-web {
    position: absolute;
    left: 0; right: 0; bottom: 42px;
    display: flex;
    align-items: center;
    justify-content: center;
    gap: 14px;
    font-size: 15px;
    letter-spacing: .03em;
  }
  .front-web__rule {
    width: 110px; height: 1px;
    background: var(--blue);
  }

  .card--back .wordmark {
    position: absolute;
    left: 40px; top: 145px;
    font-size: 32px;
    gap: 12px;
  }
  .card--back .wordmark__dot { width: 18px; height: 18px; }
  .divider {
    position: absolute;
    left: 310px; top: 75px;
    width: 2px; height: 190px;
    background: var(--ink);
    opacity: .85;
  }
  .contact {
    position: absolute;
    left: 338px; top: 68px;
    width: 260px;
  }
  .contact__name {
    font-size: 24px;
    font-weight: 500;
    color: var(--blue);
    letter-spacing: .06em;
    text-transform: uppercase;
    white-space: nowrap;
  }
  .contact__role {
    font-size: 15px;
    color: var(--ink);
    margin-top: 2px;
    letter-spacing: .03em;
  }
  .contact__address {
    font-size: 15px;
    line-height: 1.55;
    margin-top: 14px;
    letter-spacing: .03em;
    font-style: normal;
  }
  .contact__list { list-style: none; margin-top: 8px; }
  .contact__item {
    display: flex;
    align-items: center;
    gap: 9px;
    font-size: 15px;
    line-height: 1.65;
    letter-spacing: .03em;
    white-space: nowrap;
  }
  .contact__icon { width: 11px; height: 11px; flex: none; }
  .accent { color: var(--blue); }
</style>
</head>
<body>
  <section class="card card--front" aria-label="Card front">
    <div class="wordmark"><span class="wordmark__dot"></span><span class="wordmark__text">ORVEN<br>PARTNERS</span></div>
    <div class="front-web">
      <span class="front-web__rule"></span>
      <span>www.orvenpartners.com</span>
      <span class="front-web__rule"></span>
    </div>
  </section>

  <section class="card card--back" aria-label="Card back">
    <div class="wordmark"><span class="wordmark__dot"></span><span class="wordmark__text">ORVEN<br>PARTNERS</span></div>
    <div class="divider"></div>
    <div class="contact">
      <h1 class="contact__name">Daniel Harwick</h1>
      <p class="contact__role">Director</p>
      <address class="contact__address">48b Harlow Lane,<br>Wellford, NZ, 6021</address>
      <ul class="contact__list">
        <li class="contact__item">
          <svg class="contact__icon" viewBox="0 0 12 12" aria-hidden="true"><path d="M2.5 1h2l1 3-1.3 1a6.5 6.5 0 0 0 2.8 2.8l1-1.3 3 1v2a1 1 0 0 1-1 1A9.5 9.5 0 0 1 1.5 2a1 1 0 0 1 1-1z" fill="#3276b5"/></svg>
          (555) 014-2280
        </li>
        <li class="contact__item">
          <svg class="contact__icon" viewBox="0 0 12 12" aria-hidden="true"><rect x="1" y="2.5" width="10" height="7" fill="none" stroke="#3276b5" stroke-width="1.2"/><path d="M1 2.8 6 6.6l5-3.8" fill="none" stroke="#3276b5" stroke-width="1.2"/></svg>
          info@orvenpartners.com
        </li>
        <li class="contact__item">
          <svg class="contact__icon" viewBox="0 0 12 12" aria-hidden="true"><circle cx="6" cy="6" r="5" fill="none" stroke="#3276b5" stroke-width="1.2"/><ellipse cx="6" cy="6" rx="2.2" ry="5" fill="none" stroke="#3276b5" stroke-width="1"/><path d="M1 6h10" stroke="#3276b5" stroke-width="1"/></svg>
          <span>www.<span class="accent">orvenpartners</span>.com</span>
        </li>
      </ul>
    </div>
  </section>
</body>
</html>
```